Brindle Sky Port needs a new upscale business card design for our high end aircraft hangar complex

Brindle Sky Port (BSP) is a large, upscale jet hangar complex in the US housing expensive aircraft. We need a new business card design, using our current logo. We will be attending a industry convention and need a card design that will stand out and be remembered by aircraft owners and private pilots.

Target Market(s)

Aircraft pilots or owners looking for a new upscale hangar

Industry/Entity Type

Airport

Contact Information for Business Card

I like to use very heavy card stock, 400#, double sided. Square, no rounded edges please.

Colors
3276b5
0255a3
85abd2

Requirements
Must have
• An expensive, classy design, vivid colors.
Nice to have
• Needs to look very expensive and classy, and have some "pop". Designer must be able to download or copy my current typeface or fonts.
• One card side might be black with the "Logo and Brindle Sky Port Double line image in blue (or try gold, or glossy black), and perhaps have a grayed out "K720 jet silhouette". The other card side would have our contact info, and perhaps the "BSP Logo only". I'd like my contact info 'stacked', not in a paragraph format.
Should not have
• Should not look "too busy". Having a double-sided card will help.

```html
<!DOCTYPE html>
<html lang="en">
<head>
<meta charset="utf-8">
<title>Brindle Sky Port — Business Card</title>
<link rel="stylesheet" href="https://fonts.googleapis.com/css2?family=Arimo:wght@400;700&display=swap">
<style>
  :root {
    --page-bg: #a3a4a5;
    --card-black: #0f0f10;
    --brand-blue: #2a5f93;
    --band-blue-light: #2d6aa5;
    --band-blue-dark: #0c3766;
    --back-blue-center: #2a6199;
    --back-blue-edge: #0a3462;
    --text-light: #e9ecef;
    --text-white: #ffffff;
  }
  * { margin: 0; padding: 0; box-sizing: border-box; }
  html, body {
    width: 1105px; height: 1200px; overflow: hidden;
    background: var(--page-bg);
    font-family: "Arimo", Arial, sans-serif;
  }
  .canvas { position: relative; width: 1105px; height: 1200px; }

  .card {
    position: absolute; left: 178px; width: 750px; height: 428px; overflow: hidden;
  }
  .card--front { top: 119px; background: var(--card-black); }
  .card--back {
    top: 635px;
    background: radial-gradient(ellipse at 50% 40%, var(--back-blue-center) 0%, var(--back-blue-edge) 80%);
  }

  .card__bands { position: absolute; inset: 0; }

  .brand-mark {
    position: absolute; display: flex; align-items: center; gap: 10px;
    font-weight: 700; white-space: nowrap;
  }
  .brand-mark__square { display: block; background: currentColor; }
  .card--front .brand-mark {
    left: 96px; top: 201px; color: var(--brand-blue); font-size: 28px;
  }
  .card--front .brand-mark__square { width: 18px; height: 18px; }
  .card--back .brand-mark {
    left: 0; right: 0; top: 180px; justify-content: center;
    color: var(--text-white); font-size: 42px;
  }
  .card--back .brand-mark__square { width: 26px; height: 26px; }

  .contact { position: absolute; left: 421px; top: 78px; color: var(--text-light); }
  .contact__name { font-size: 25px; color: var(--band-blue-light); line-height: 1; }
  .contact__title { font-size: 20px; margin-top: 9px; line-height: 1; }
  .contact__address { font-size: 18.5px; line-height: 25px; margin-top: 17px; }
  .contact__list { list-style: none; margin-top: 16px; }
  .contact__item {
    display: flex; align-items: center; gap: 14px;
    font-size: 18.5px; height: 29px;
  }
  .contact__icon { width: 21px; height: 21px; flex: none; fill: var(--brand-blue); }

  .card__web {
    position: absolute; left: 0; right: 0; top: 360px; text-align: center;
    color: var(--text-light); font-size: 18px; letter-spacing: 4px;
  }
</style>
</head>
<body>
<div class="canvas">

  <section class="card card--front" aria-label="Card front">
    <svg class="card__bands" width="750" height="428" viewBox="0 0 750 428" aria-hidden="true">
      <defs>
        <linearGradient id="band-top" x1="0" y1="0" x2="1" y2="0">
          <stop offset="0" stop-color="var(--band-blue-light)"/>
          <stop offset="1" stop-color="var(--band-blue-dark)"/>
        </linearGradient>
        <linearGradient id="band-bottom" x1="0" y1="0" x2="1" y2="0">
          <stop offset="0" stop-color="var(--band-blue-light)"/>
          <stop offset="1" stop-color="var(--band-blue-dark)"/>
        </linearGradient>
      </defs>
      <path d="M60 0 H750 V29 H100 Q78 29 60 0 Z" fill="url(#band-top)"/>
      <path d="M0 399 H640 Q662 399 680 428 H0 Z" fill="url(#band-bottom)"/>
    </svg>

    <div class="brand-mark"><span class="brand-mark__square"></span>Brindle Sky Port</div>

    <div class="contact">
      <p class="contact__name">Dana Whitlow</p>
      <p class="contact__title">President</p>
      <p class="contact__address">2716 Harrow Lane<br>Cedar Bluff, NY 11040</p>
      <ul class="contact__list">
        <li class="contact__item">
          <svg class="contact__icon" viewBox="0 0 24 24" aria-hidden="true"><path d="M2 9c0-3 4-5 10-5s10 2 10 5v2h-5V8H7v3H2z M5 13h14l2 8H3z"/></svg>
          555 0142 7731</li>
        <li class="contact__item">
          <svg class="contact__icon" viewBox="0 0 24 24" aria-hidden="true"><path d="M7 2h10a1 1 0 0 1 1 1v18a1 1 0 0 1-1 1H7a1 1 0 0 1-1-1V3a1 1 0 0 1 1-1zm1 3v12h8V5zm3 14v1h2v-1z"/></svg>
          555 0198 2046</li>
        <li class="contact__item">
          <svg class="contact__icon" viewBox="0 0 24 24" aria-hidden="true"><path d="M7 2h10v6H7z M3 9h18v9h-3v4H6v-4H3z M8 15v5h8v-5z"/></svg>
          555 0167 3390</li>
        <li class="contact__item">
          <svg class="contact__icon" viewBox="0 0 24 24" aria-hidden="true"><path d="M2 5h20v2l-10 6L2 7z M2 9l10 6 10-6v10H2z"/></svg>
          dana@skyport-mail.com</li>
        <li class="contact__item">
          <svg class="contact__icon" viewBox="0 0 24 24" aria-hidden="true"><path d="M12 2a10 10 0 1 0 0 20 10 10 0 0 0 0-20zm-2 4 3 2-1 3-3 1-2-3zm5 7 3 1-2 4-3-1z"/></svg>
          www.skyport-mail.com</li>
      </ul>
    </div>
  </section>

  <section class="card card--back" aria-label="Card back">
    <div class="brand-mark"><span class="brand-mark__square"></span>Brindle Sky Port</div>
    <p class="card__web">www.skyport-mail.com</p>
  </section>

</div>
</body>
</html>
```